Tech business card design

We need an amazing business card design for our new business 'Pexla' a marketing tech startup based in Sydney, Australia. We provide an online marketplace for businesses to search and buy advertising media, connect with service providers and learn more about marketing. We wish to communicate 'cool tech', reliability and professionalism and design based around our logo.

Target Market(s)

Business Owners

Contact Information for Business Card

Name
Position
Email Address
Website
Phone Number

Font styles to use
Other font styles liked:
• Avenir & Avenir Next

Colors

Designer to choose colors to be used in the design.

```html
<!DOCTYPE html>
<html lang="en">
<head>
<meta charset="utf-8">
<title>Pexla Business Card</title>
<link rel="stylesheet" href="https://fonts.googleapis.com/css2?family=Source+Sans+3:wght@400;700;900&display=swap">
<style>
  :root {
    --page: #e1dedf;
    --card: #d9d9e3;
    --ink: #13133f;
    --text: #23234a;
    --stripe-dark: #2a3373;
    --stripe-mid: #8e96b8;
    --stripe-light: #f4f4f8;
  }
  * { box-sizing: border-box; margin: 0; padding: 0; }
  html, body { width: 975px; height: 1200px; overflow: hidden; }
  body {
    background: var(--page);
    font-family: "Source Sans 3", "Myriad Pro", sans-serif;
    color: var(--text);
    position: relative;
  }
  .card {
    position: absolute;
    left: 58px;
    width: 859px;
    height: 491px;
    background: var(--card);
  }
  .card--front { top: 84px; }
  .card--back { top: 636px; }
  .stripe {
    position: absolute;
    left: 0;
    width: 100%;
    height: 10px;
    background: linear-gradient(90deg,
      var(--stripe-dark) 0%,
      var(--stripe-mid) 18%,
      var(--stripe-light) 31%,
      #c2c6d8 38%,
      var(--stripe-mid) 52%,
      var(--stripe-dark) 68%,
      var(--stripe-mid) 86%,
      var(--stripe-light) 100%);
  }
  .holder {
    position: absolute;
    top: 92px;
    width: 100%;
    text-align: center;
    line-height: 1;
  }
  .holder__name { font-weight: 700; font-size: 29px; letter-spacing: 0.2px; }
  .holder__role { font-weight: 400; font-size: 25px; margin-top: 8px; }
  .wordmark {
    position: absolute;
    font-weight: 900;
    color: var(--ink);
    line-height: 1;
    letter-spacing: -1px;
  }
  .card--front .wordmark { left: 68px; top: 380px; font-size: 118px; }
  .card--back .wordmark { left: 0; width: 100%; text-align: center; top: 200px; font-size: 158px; }
  .contacts {
    position: absolute;
    right: 60px;
    top: 282px;
    font-size: 21px;
    line-height: 1;
  }
  .contacts__row { display: flex; align-items: center; gap: 7px; height: 33px; }
  .contacts__row svg { width: 20px; height: 20px; flex: none; }
  .contacts__address { margin-top: 7px; text-align: right; line-height: 29px; }
  .web {
    position: absolute;
    top: 1076px;
    left: 0;
    width: 100%;
    text-align: center;
    font-size: 26px;
    letter-spacing: 4px;
    line-height: 1;
  }
</style>
</head>
<body>
  <section class="card card--front">
    <div class="holder">
      <p class="holder__name">JOHN SMITH</p>
      <p class="holder__role">Position</p>
    </div>
    <div class="stripe" style="top:227px"></div>
    <div class="wordmark" style="top:300px">Pexla</div>
    <div class="contacts">
      <div class="contacts__row">
        <svg viewBox="0 0 20 20" aria-hidden="true"><circle cx="10" cy="10" r="8.5" fill="none" stroke="currentColor" stroke-width="1.6"/><path d="M6.5 5.5l2 0.2 0.8 2.3-1.2 1a6 6 0 0 0 3 3l1-1.2 2.3.8.2 2c-.5.8-1.5 1-2.4.8A8 8 0 0 1 5.7 7.9c-.2-.9 0-1.9.8-2.4z" fill="currentColor"/></svg>
        <span>012-345-6789</span>
      </div>
      <div class="contacts__row">
        <svg viewBox="0 0 20 20" aria-hidden="true"><rect x="2" y="5" width="16" height="11" fill="currentColor"/><path d="M2.5 5.5L10 11l7.5-5.5M2.5 15.5l5.5-5M17.5 15.5l-5.5-5" fill="none" stroke="#d9d9e3" stroke-width="1.3"/></svg>
        <span>info@pexla.com</span>
      </div>
      <div class="contacts__row">
        <svg viewBox="0 0 20 20" aria-hidden="true" fill="none" stroke="currentColor" stroke-width="1.4"><circle cx="10" cy="10" r="8.3"/><ellipse cx="10" cy="10" rx="3.8" ry="8.3"/><path d="M1.7 10h16.6M3 6h14M3 14h14M10 1.7v16.6"/></svg>
        <span>www.pexla.com</span>
      </div>
      <p class="contacts__address">Street name City Name<br>Zipcode,012345</p>
    </div>
  </section>

  <section class="card card--back">
    <div class="stripe" style="top:84px"></div>
    <div class="wordmark" style="top:170px">Pexla</div>
    <div class="stripe" style="top:409px"></div>
  </section>
  <p class="web">www.pexla.com</p>
</body>
</html>
```